New business card, letter head, email signature and Portfolio for our Security company.

We are an Crest security company that provides a top quality manpower services to protect high rise buildings, retail and all type of properties and would like a new business card/logo look.

- We would like the spot UV design.
- Matt black (double sided).
- We would like to incorporate a royal blue colour (feel free to experiment with it).
- Feel free to try different lengths with the card to make it stand out more than a normal business card.
- We would like the logo to be an eagle eye in the background (shines when card is tilted slightly in the background, either on the front, back or both sides of the card). Image attached as an example of eye shape (colour to be either black or royal blue).
- HARBOUR CREST SECURITY SERVICES PTY. LTD. and HCSS to be placed on one side of the card and on the other side of the card to have;

- Name in slightly bigger font than the position (directly on the bottom on the name).
- Mobile number
- Email address
- Website email address
- PO BOX address

Can we please have the files in a format that we can edit.

Reason: I need to consult my business partner with the designs so far and will make a decision from there.

Target Market(s)

Security Industry

Industry/Entity Type

Business

Contact Information for Business Card

- Mobile number
- Email address
- Website email address
- PO BOX address

Logo Text

HCSS and underneath the HCSS please add HARBOUR CREST SECURITY SERVICES PTY. LTD.

Font styles to use
Other font styles liked:
• bold type font

Colors
0255a3
000000

Requirements
Must have
• We are an Crest security company that provides a top quality manpower services to protect high rise buildings, retail and all type of properties and would like a new business card/logo look.
• - We would like the spot UV design.
• - Matt black (double sided).
• - We would like to incorporate a royal blue colour (feel free to experiment with it).
• - Feel free to try different lengths with the card to make it stand out more than a normal business card.
• - We would like the logo to be an eagle eye in the background (shines when card is tilted slightly in the background, either on the front, back or both sides of the card). Image attached as an example of eye shape (colour to be either black or royal blue).
• - HARBOUR CREST SECURITY SERVICES PTY. LTD. and HCSS to be placed on one side of the card and on the other side of the card to have;
• - Name in slightly bigger font than the position (directly on the bottom on the name).
• - Mobile number
• - Email address
• - Website email address
• - PO BOX address
• Can we please have the files in a format that we can edit.
Nice to have
• Feel free to try different lengths with the card to make it stand out more than a normal business card.
• Please find "URBAN JUNGLE" font attached and incorporate HCSS into the same style with building's inside the HCSS bold front also add HARBOUR into the bottom part of the S and follow on E - Crest on the bottom S - SECURITY on the bottom S - SERVICES on the bottom of each letter.
• other than that, I'll be happy with a bold modern font for the HCSS and HARBOUR CREST SECURITY SERVICES in a bold and thinner font underneath.

```html
<!DOCTYPE html>
<html lang="en">
<head>
<meta charset="utf-8">
<title>Harbour Crest Security – Business Card</title>
<link rel="stylesheet" href="https://fonts.googleapis.com/css2?family=Exo+2:wght@700;800&family=Open+Sans:wght@400;600&display=swap">
<style>
  :root {
    --canvas: #d9d9d9;
    --card: #2b2b2d;
    --card-deep: #1e1e20;
    --band: #1a1a1c;
    --gloss-light: #8a8a8d;
    --gloss-dark: #3a3a3c;
    --white: #ffffff;
    --text-soft: #e6e6e6;
    --royal: #2a3bb0;
    --royal-line: #3445c4;
  }
  * { margin: 0; padding: 0; box-sizing: border-box; }
  html, body {
    width: 1200px; height: 1000px; overflow: hidden;
    background: var(--canvas);
  }
  .canvas { position: relative; width: 1200px; height: 1000px; }

  .card {
    position: absolute; left: 200px; width: 800px; height: 457px;
    background: var(--card);
    overflow: hidden;
    box-shadow: 0 10px 28px rgba(0,0,0,.28);
  }
  .card--back { top: 30px; }
  .card--front { top: 513px; }

  /* Back side */
  .back-pattern {
    position: absolute; inset: 0;
    background: linear-gradient(115deg, var(--gloss-light) 0%, var(--gloss-dark) 38%, var(--card-deep) 100%);
    opacity: .55;
  }
  .back-band {
    position: absolute; left: 0; right: 0; top: 150px; height: 190px;
    background: linear-gradient(180deg, var(--band), #242426);
    display: flex; flex-direction: column; align-items: center; justify-content: center;
  }
  .brand-dot {
    width: 34px; height: 34px; border-radius: 50%;
    background: var(--royal); margin-bottom: 14px;
  }
  .brand-name {
    font-family: "Exo 2", sans-serif; font-weight: 800;
    font-size: 36px; letter-spacing: 1px; color: var(--white);
    line-height: 1;
  }
  .brand-sub {
    display: flex; align-items: center; gap: 12px; margin-top: 6px;
    font-family: "Open Sans", sans-serif; font-weight: 600;
    font-size: 12px; letter-spacing: 1.5px; color: var(--text-soft);
  }
  .brand-sub::before, .brand-sub::after {
    content: ""; width: 80px; height: 2px; background: var(--royal-line);
  }

  /* Front side */
  .eye-mark {
    position: absolute; left: -20px; top: 90px; width: 470px; height: 300px;
    border-radius: 50% 60% 40% 50%;
    background: radial-gradient(ellipse at 70% 30%, #9a9a9d 0%, #5c5c5f 40%, #262628 85%);
    opacity: .9;
  }
  .details {
    position: absolute; right: 36px; top: 70px;
    text-align: right;
    font-family: "Open Sans", sans-serif; color: var(--text-soft);
  }
  .company {
    font-family: "Exo 2", sans-serif; font-weight: 800;
    font-size: 30px; letter-spacing: .5px; color: var(--white); line-height: 1;
  }
  .company-sub {
    font-size: 10px; font-weight: 600; letter-spacing: 1.2px; margin-top: 3px;
  }
  .person {
    margin-top: 48px;
    font-family: "Exo 2", sans-serif; font-weight: 700;
    font-size: 32px; letter-spacing: 3px; color: var(--royal); line-height: 1;
  }
  .role { font-size: 20px; letter-spacing: 2px; color: var(--white); margin-top: 4px; }
  .address { margin-top: 22px; font-size: 18px; line-height: 1.3; letter-spacing: .5px; }
  .contact { list-style: none; margin-top: 14px; font-size: 18px; letter-spacing: .5px; }
  .contact li { display: flex; justify-content: flex-end; align-items: center; gap: 12px; line-height: 1.45; }
  .contact svg { width: 14px; height: 14px; fill: var(--royal); flex: none; }
  .accent { color: var(--royal); }
</style>
</head>
<body>
<main class="canvas">

  <section class="card card--back">
    <div class="back-pattern" role="img" aria-label="Repeated spot UV eye emblem pattern in glossy grey"></div>
    <div class="back-band">
      <div class="brand-dot"></div>
      <div class="brand-name">HARBOUR CREST SECURITY</div>
      <div class="brand-sub">SERVICES PTY. LTD. and HCSS</div>
    </div>
  </section>

  <section class="card card--front">
    <div class="eye-mark" role="img" aria-label="Large glossy spot UV eye emblem"></div>
    <div class="details">
      <div class="company">HARBOUR CREST SECURITY</div>
      <div class="company-sub">SERVICES PTY. LTD. and HCSS</div>
      <div class="person">DANIEL HARTE</div>
      <div class="role">OWNER</div>
      <p class="address">PO Box 482,<br>Singapore, 9012</p>
      <ul class="contact">
        <li>+000 987 654 321
          <svg viewBox="0 0 24 24"><path d="M6.6 10.8a15 15 0 0 0 6.6 6.6l2.2-2.2c.3-.3.7-.4 1-.2 1.1.4 2.3.6 3.6.6.6 0 1 .4 1 1V20c0 .6-.4 1-1 1A17 17 0 0 1 3 4c0-.6.4-1 1-1h3.5c.6 0 1 .4 1 1 0 1.3.2 2.5.6 3.6.1.3 0 .7-.2 1z"/></svg></li>
        <li>daniel@harbourcrest.com
          <svg viewBox="0 0 24 24"><path d="M2 5h20v14H2zM4 7v1l8 5 8-5V7l-8 5z"/></svg></li>
        <li><span>www.<span class="accent">harbourcrest</span>.com</span>
          <svg viewBox="0 0 24 24"><path d="M14 3a7 7 0 1 1-4.9 12L4 20.1 2.6 18.7 7.7 13.6A7 7 0 0 1 14 3zm0 2.5a4.5 4.5 0 1 0 0 9 4.5 4.5 0 0 0 0-9z"/></svg></li>
      </ul>
    </div>
  </section>

</main>
</body>
</html>
```